COMPANY NAME: Bright Harbor Ventures: Task Description: We are a new UK based business with global rea

Target Market

- Personal and professional development – 30-55 age group, corporate leaders, Eastern European and Asian markets
- On-assignment projects – Corporate market – Eastern European and Asian Markets
- Property investment - 35-65 age group, Europe, USA, Australia

What we need

We need logos and brand design for a suite of web platforms (website, twitter and Facebook profile). We would like to have a cohesive and consistent look across all of our online platforms. The design suite must therefore include social media logos, backgrounds and headers. Specifically we are looking for:

a. Facebook header/page design: likely to have a more youthful look

b. Website: Header, background and layout that is responsive to devices, iPhone primarily, then tablet, then PC (we have purchased a website building package from SiteKettle so if you are familiar with one of their themes, it would be great to have a design that fits with a theme you would recommend); Design should be able to accommodate a place to position video in the medium term but an image in the short term.

c. LinkedIn: header/logo; more corporate look

d. Twitter: background/logo

e. Powerpoint template: background and logo - simple and soft background not busy

f. Electronic Newsletter: logo, header and sidebar; simple and soft background not busy

h. Business card: sophisticated and simple

Colors

We have in mind a preference for colors from the purple family, maybe lavender, so as to appeal to all genders and age groups. Though we are happy to go with a recommendation if you think otherwise.

We would like a look that is professional, airy, bright, fresh, futuristic, insightful, friendly.

Ethos of the brand

- experiencing opportunity and being fulfilled in a changing world
- services are facilitated through insights
- support provided through our product, services and tailored approach to coaching/partnerships (which includes private client match-making)
- we are service providers and passionate about quality and modern leadership skills at all stages in life.

The company name is "Bright Harbor Ventures” - our main message is helping people move to the next level - through investments, personal and professional growth.

Some of our messaging

1. International Leadership in a new world.

2. New technology;

3. Informed;

4. Positively Influential

5. Making a difference;

6. Empowered;

7. Risk free investments;

8. Commercial opportunity;

9. Fulfilled living;

10. Carefree and Fun Living;

11. Progression;

12. Open-minded

13. Energy/dynamic

The Business:
The business is to move people very quickly out of situations that hold them back. the situations could be their own personal situations; their career; their jobs; their teams; their ideas; their finances; their financial opportunities. Remove their fears and give them the strategies to take action. The team are international and have 40 years experience between them in this area.

We do want to come across modern and dynamic, customer outcome focussed, building long-term relationships; international.
Updates

Project Deadline Extended
Reason: We have not found the right designs - we are not just looking for a website design but also images and logos. Most images we can see in the designs are stock images - very standard. We need an image which will be the face of the company, like the shop front window. This main image will be used on social media (top image) and also the home page of the website.

Target Market(s)

30-55 years
Eastern Europe; UK; Asia; Africa; Middle East
Personal, Professional, Corporate, and Financial Growth

Industry/Entity Type

Business Service

Contact Information for Business Card

Simple and stylish
the 3 areas of the business on the reverse -

International look - Offices in UK and San Francisco

Company name
web address www.brightharborventure.com
email director@brightharborventure.com
Facebook bright harbor venture
LinkedIn Bright Harbor Venture
Twitter Bright Harbor Venture
Telephone: +44 (0) 768 213 5597

Logo Text

Something that symbolises unlimited growth - probably not text - could use the word INSIGHT in some way

Number of Pages Required

1 page

Colors
e4daeb
f3f1f8
ffffff

Requirements
Must have
• social media symbols and address
• company name
• Melanie Thorpe
• Director
• Telephone +44 (0) 768 213 5597
• Website name www.brightharborventure.co.uk
• Reverse of Card:
• Discreet, Fast, Bright Harbor Consultancy
• Corporate, Professional, Personal & Property Investment
Nice to have
• not too angular; soft lines; not too cluttered (possibly social media on the reverse and just logo, name, number on the front?
Should not have
• too busy

```html
<!DOCTYPE html>
<html lang="en">
<head>
<meta charset="utf-8">
<title>Bright Harbor Venture</title>
<link href="https://fonts.googleapis.com/css2?family=Open+Sans:ital,wght@0,400;0,600;0,700;0,800;1,400&family=Roboto+Condensed:wght@700&display=swap" rel="stylesheet">
<style>
:root{
  --lavender:#e4daeb;
  --mist:#f3f1f8;
  --white:#ffffff;
  --ink:#3d3d3d;
  --text:#5a5a5a;
  --muted:#8a8a8a;
  --night:#1c1c1c;
  --line:#e2dde6;
}
*{box-sizing:border-box;margin:0;padding:0}
html,body{width:1200px;height:2679px;overflow:hidden}
body{font-family:"Open Sans",Arial,sans-serif;color:var(--text);background:var(--white);position:relative}
.section{position:absolute;left:0;width:1200px}
svg{display:block}

/* top bar */
.topbar{top:0;height:54px;background:var(--mist);font-size:13px;color:#555;font-weight:600}
.topbar .contact{position:absolute;left:75px;top:0;height:54px;display:flex;align-items:center;gap:12px}
.topbar .contact span{display:flex;align-items:center;gap:9px}
.topbar .sep{color:#999}
.search{position:absolute;left:888px;top:0;width:312px;height:54px;border-left:1px solid var(--line);display:flex;align-items:center;padding-left:24px;color:#888;font-size:12px;font-weight:400}
.search svg{position:absolute;right:42px;top:17px}

/* header */
.header{top:54px;height:76px;background:var(--white)}
.header .close{position:absolute;left:76px;top:27px}
.brand{position:absolute;left:0;width:1200px;top:0;height:76px;line-height:76px;text-align:center;font-family:"Roboto Condensed",Arial,sans-serif;font-weight:700;font-size:27px;color:#333;letter-spacing:.3px}
.social{position:absolute;right:75px;top:30px;display:flex;gap:18px}
.social i{width:16px;height:16px;border-radius:50%;background:#8b8b8b;display:block}

/* hero */
.hero{top:130px;height:527px;overflow:hidden}
.hero .photo{position:absolute;inset:0;background:linear-gradient(180deg,#e6e3e8 0%,#c8c2cc 35%,#8f8796 70%,#6e6674 100%)}
.hero-title{position:absolute;left:0;width:1200px;top:195px;text-align:center;color:var(--white);font-weight:800;font-size:64px;letter-spacing:1px;line-height:78px}
.hero-sub{position:absolute;left:0;width:1200px;top:268px;text-align:center;color:var(--white);font-weight:700;font-size:26px}
.menu{position:absolute;left:75px;top:0;width:243px;height:365px;background:var(--night);z-index:2;list-style:none;padding-top:23px}
.menu li{height:49px;line-height:22px;padding-left:30px;color:var(--white);font-size:11.5px;text-transform:uppercase;letter-spacing:.2px}
.dots{position:absolute;left:566px;top:486px;display:flex;gap:7px}
.dots i{width:10px;height:10px;border-radius:50%;background:#2a2a2a;display:block}
.dots i:first-child{background:var(--white)}

/* buttons */
.btn{display:inline-block;height:43px;line-height:43px;padding:0 30px;background:var(--lavender);color:#4a4a4a;font-size:14px;font-weight:700;text-transform:uppercase;letter-spacing:.3px}

/* welcome */
.welcome{top:657px;height:384px;text-align:center}
.welcome h2{margin-top:46px;font-size:30px;font-weight:600;color:var(--ink);letter-spacing:.5px}
.welcome .lead{margin-top:22px;font-size:15.5px;font-weight:700;color:#444}
.welcome p{font-size:15px;line-height:27px;max-width:1050px;margin:4px auto 0}
.welcome p + p{margin-top:8px}
.welcome .btn{margin-top:42px}

/* services */
.services{top:1041px;height:418px;background:var(--mist)}
.card{position:absolute;top:50px;height:320px;background:var(--white);padding:29px 21px 0}
.card .head{display:flex;align-items:center;gap:17px;height:54px}
.card .icon{width:54px;height:54px;border:1px solid #ddd;display:flex;align-items:center;justify-content:center}
.card h3{font-size:17px;font-weight:700;color:#333;line-height:23px;letter-spacing:.3px}
.card ul{list-style:none;margin-top:36px}
.card li{display:flex;gap:13px;font-size:14.5px;line-height:20px;margin-bottom:14px;color:#555}
.card li svg{flex:none;margin-top:4px}
.card .btn{position:absolute;left:21px;top:241px;width:152px;text-align:center;padding:0}

/* features */
.features{top:1459px;height:425px}
.features h2{position:absolute;left:75px;top:64px;font-size:30px;font-weight:600;color:var(--ink);letter-spacing:.5px}
.features p{position:absolute;left:75px;top:120px;width:520px;font-size:15px;line-height:31.5px}
.features .btn{position:absolute;left:75px;top:314px;padding:0 16px}
.video{position:absolute;left:614px;top:55px;width:513px;height:317px;background:linear-gradient(135deg,#eae8ec 0%,#d6d3da 45%,#b9b5bf 100%)}
.video svg{position:absolute;left:220px;top:132px}

/* news */
.news{top:1884px;height:486px;background:linear-gradient(180deg,#efedf4 0%,#f6f4f9 60%,#ffffff 100%)}
.news h2{position:absolute;left:75px;top:44px;font-size:30px;font-weight:600;color:var(--ink);letter-spacing:.5px}
.item{position:absolute;left:75px;width:690px}
.date{position:absolute;left:0;top:0;width:75px;height:80px;background:var(--white);text-align:center}
.date .m{display:block;height:24px;line-height:24px;background:var(--lavender);font-size:13px;font-weight:700;color:#444}
.date .d{display:block;font-size:32px;font-weight:700;color:#333;line-height:54px}
.item h4{margin-left:104px;font-size:16.5px;font-weight:700;color:#333;line-height:20px}
.item p{margin-left:104px;font-size:14.5px;line-height:24px;margin-top:3px}
.item .more{margin-left:104px;font-size:12.5px;font-weight:700;color:#333;display:block;margin-top:2px}
.divider{position:absolute;left:75px;top:225px;width:690px;height:1px;background:var(--line)}
.news .all{position:absolute;left:164px;top:386px;padding:0 18px}
.testimonial{position:absolute;left:795px;top:54px;width:332px;height:378px;background:var(--white);padding:26px 21px}
.testimonial h2{position:static;font-size:30px}
.testimonial blockquote{margin-top:18px;font-style:italic;font-size:14.5px;line-height:27px;color:#555}
.testimonial .name{margin-top:20px;font-size:14.5px;font-weight:700;color:#333}
.testimonial .co{font-size:12px;color:#666;margin-top:2px}
.testimonial .btn{position:absolute;left:21px;top:306px;width:152px;text-align:center;padding:0}

/* footer */
.footer{top:2370px;height:309px;background:var(--lavender)}
.f-brand{position:absolute;left:75px;top:48px;font-family:"Roboto Condensed",Arial,sans-serif;font-weight:700;font-size:25px;color:#777}
.f-legal{position:absolute;left:75px;top:101px;font-size:12.5px;line-height:24px;color:#555}
.f-social{position:absolute;left:75px;top:202px;display:flex;gap:20px}
.f-social i{width:15px;height:15px;border-radius:50%;background:#5a5a5a;display:block}
.footer h5{font-size:14px;font-weight:700;color:#555;text-transform:uppercase;letter-spacing:.3px}
.sitemap{position:absolute;left:436px;top:53px}
.links{display:grid;grid-template-columns:150px 150px;margin-top:15px;row-gap:6px}
.links a{font-size:14px;color:#555;text-decoration:none;line-height:24px}
.chat{position:absolute;left:766px;top:53px;width:370px}
.chat p{margin-top:11px;font-size:13.5px;line-height:22px;color:#555}
.chat .row{display:flex;align-items:center;gap:12px;margin-top:12px;font-size:13.5px;font-weight:700;color:#444}
</style>
</head>
<body>

<div class="section topbar">
  <div class="contact">
    <span><svg width="12" height="12" viewBox="0 0 24 24"><path fill="#666" d="M6.6 10.8a15 15 0 0 0 6.6 6.6l2.2-2.2c.3-.3.7-.4 1-.2 1.1.4 2.3.6 3.6.6.6 0 1 .4 1 1V20c0 .6-.4 1-1 1A17 17 0 0 1 3 4c0-.6.4-1 1-1h3.5c.6 0 1 .4 1 1 0 1.3.2 2.5.6 3.6.1.3 0 .7-.2 1z"/></svg>+44 (0) 768 213 5597</span>
    <span class="sep">|</span>
    <span><svg width="13" height="11" viewBox="0 0 26 20"><rect x="1" y="1" width="24" height="18" rx="2" fill="#666"/><path d="M2 3l11 8 11-8" stroke="#f3f1f8" stroke-width="2" fill="none"/></svg>director@brightharborventure.com</span>
  </div>
  <div class="search">Search...
    <svg width="20" height="20" viewBox="0 0 20 20"><circle cx="8" cy="8" r="6" stroke="#888" stroke-width="2.4" fill="none"/><path d="M12.5 12.5l5.5 5.5" stroke="#888" stroke-width="2.6" stroke-linecap="round"/></svg>
  </div>
</div>

<div class="section header">
  <svg class="close" width="22" height="22" viewBox="0 0 22 22"><path d="M3 3l16 16M19 3L3 19" stroke="#555" stroke-width="4.5" stroke-linecap="round"/></svg>
  <div class="brand">BRIGHT HARBOR VENTURE</div>
  <div class="social"><i></i><i></i><i></i><i></i><i></i></div>
</div>

<div class="section hero">
  <div class="photo" role="img" aria-label="City skyline of tall glass office towers under a soft pale sky"></div>
  <ul class="menu">
    <li>About You</li><li>About Us</li><li>Our Values</li><li>Testimonials</li><li>Social Media</li><li>News Alert</li><li>Contact Us</li>
  </ul>
  <div class="hero-title">BRIGHT HARBOR VENTURE</div>
  <div class="hero-sub">We are a consulting company in the UK</div>
  <div class="dots"><i></i><i></i><i></i><i></i></div>
</div>

<div class="section welcome">
  <h2>WELCOME TO BRIGHT HARBOR VENTURE</h2>
  <div class="lead">Hello and welcome to the company that works with you on your terms.</div>
  <p>If you seek an experienced and trusted partner to work with you on an assignment or simply want some strategies to move your personal or professional talents to the next level then you are in the right place.</p>
  <p>If you feel that the pace of change in business is so fast that to be an outstanding leader you should ensure you are brought up to speed regularly then you are in the right place.</p>
  <span class="btn">Read More</span>
</div>

<div class="section services">
  <div class="card" style="left:75px;width:330px">
    <div class="head">
      <div class="icon"><svg width="34" height="26" viewBox="0 0 34 26"><circle cx="17" cy="7" r="6" fill="#444"/><circle cx="6" cy="9" r="4" fill="#444"/><circle cx="28" cy="9" r="4" fill="#444"/><path d="M7 26c0-7 4-11 10-11s10 4 10 11z" fill="#444"/><path d="M0 24c0-5 2-8 6-8 2 0 3 .5 4 1.5C8 19 7 22 7 24zM34 24c0-5-2-8-6-8-2 0-3 .5-4 1.5 2 1.5 3 4.5 3 6.5z" fill="#444"/></svg></div>
      <h3>CONSULTANCY</h3>
    </div>
    <ul>
      <li><svg width="12" height="12" viewBox="0 0 12 12"><circle cx="6" cy="6" r="5" stroke="#555" stroke-width="1.4" fill="none"/><path d="M5 3.5L7.5 6 5 8.5" stroke="#555" stroke-width="1.4" fill="none"/></svg>Professional and Personal</li>
      <li><svg width="12" height="12" viewBox="0 0 12 12"><circle cx="6" cy="6" r="5" stroke="#555" stroke-width="1.4" fill="none"/><path d="M5 3.5L7.5 6 5 8.5" stroke="#555" stroke-width="1.4" fill="none"/></svg>Next Generation Leaders (16-30)</li>
      <li><svg width="12" height="12" viewBox="0 0 12 12"><circle cx="6" cy="6" r="5" stroke="#555" stroke-width="1.4" fill="none"/><path d="M5 3.5L7.5 6 5 8.5" stroke="#555" stroke-width="1.4" fill="none"/></svg>Consultation Options</li>
    </ul>
    <span class="btn">Read More</span>
  </div>
  <div class="card" style="left:436px;width:334px">
    <div class="head">
      <div class="icon"><svg width="24" height="30" viewBox="0 0 24 30"><path d="M0 0h16l8 8v22H0z" fill="#444"/><path d="M16 0v8h8" fill="#999"/><path d="M5 14h14M5 19h14M5 24h10" stroke="#fff" stroke-width="2"/></svg></div>
      <h3>ON ASSIGNMENT</h3>
    </div>
    <ul>
      <li><svg width="12" height="12" viewBox="0 0 12 12"><circle cx="6" cy="6" r="5" stroke="#555" stroke-width="1.4" fill="none"/><path d="M5 3.5L7.5 6 5 8.5" stroke="#555" stroke-width="1.4" fill="none"/></svg>Team Cohesion Strategy</li>
      <li><svg width="12" height="12" viewBox="0 0 12 12"><circle cx="6" cy="6" r="5" stroke="#555" stroke-width="1.4" fill="none"/><path d="M5 3.5L7.5 6 5 8.5" stroke="#555" stroke-width="1.4" fill="none"/></svg>Go To Market Strategy</li>
      <li><svg width="12" height="12" viewBox="0 0 12 12"><circle cx="6" cy="6" r="5" stroke="#555" stroke-width="1.4" fill="none"/><path d="M5 3.5L7.5 6 5 8.5" stroke="#555" stroke-width="1.4" fill="none"/></svg>Internationalisation Strategy</li>
    </ul>
    <span class="btn">Read More</span>
  </div>
  <div class="card" style="left:797px;width:330px">
    <div class="head">
      <div class="icon"><svg width="32" height="28" viewBox="0 0 32 28"><path d="M16 1L1 14h4v13h8v-8h6v8h8V14h4z" fill="#444"/></svg></div>
      <h3>PROPERTY:<br>PRIVATE CLIENT</h3>
    </div>
    <ul>
      <li><svg width="12" height="12" viewBox="0 0 12 12"><circle cx="6" cy="6" r="5" stroke="#555" stroke-width="1.4" fill="none"/><path d="M5 3.5L7.5 6 5 8.5" stroke="#555" stroke-width="1.4" fill="none"/></svg>Promotion and cash-buyer matching</li>
      <li><svg width="12" height="12" viewBox="0 0 12 12"><circle cx="6" cy="6" r="5" stroke="#555" stroke-width="1.4" fill="none"/><path d="M5 3.5L7.5 6 5 8.5" stroke="#555" stroke-width="1.4" fill="none"/></svg>Investment: high return projects</li>
      <li><svg width="12" height="12" viewBox="0 0 12 12"><circle cx="6" cy="6" r="5" stroke="#555" stroke-width="1.4" fill="none"/><path d="M5 3.5L7.5 6 5 8.5" stroke="#555" stroke-width="1.4" fill="none"/></svg>Commercial: Hotels and Senior<br>Housing</li>
    </ul>
    <span class="btn">Read More</span>
  </div>
</div>

<div class="section features">
  <h2>OUR FEATURES</h2>
  <p>Aliquam molestie, mi et imperdiet euismod, dui purus auctor tellus, et interdum lacus lectus et ante. Sed accumsan sollicitudin sapien, sit amet adipiscing turpis gravida ac. In congue, neque ac lobortis volutpat, libero mauris varius mi, vitae suscipit ipsum ligula vitae risus. Duis aliquam nibh a dui iaculis viverra id a velit.</p>
  <span class="btn">Watch a Video</span>
  <div class="video" role="img" aria-label="Video still of business people reviewing charts on a tablet at a desk">
    <svg width="72" height="50" viewBox="0 0 72 50"><rect width="72" height="50" rx="10" fill="#fff"/><path d="M29 14l17 11-17 11z" fill="#555"/></svg>
  </div>
</div>

<div class="section news">
  <h2>NEWS ALERT</h2>
  <div class="item" style="top:107px">
    <div class="date"><span class="m">SEP</span><span class="d">26</span></div>
    <h4>Aliquam molestie mi et imperdiet euismod</h4>
    <p>Dui purus auctor tellus, et interdum lacus lectus et antesed accumsan sollicitudin sapien, sit amet adipiscing turpis gravida ac.</p>
    <span class="more">Read More</span>
  </div>
  <div class="divider"></div>
  <div class="item" style="top:250px">
    <div class="date"><span class="m">SEP</span><span class="d">26</span></div>
    <h4>Aliquam molestie mi et imperdiet euismod</h4>
    <p>Dui purus auctor tellus, et interdum lacus lectus et antesed accumsan sollicitudin sapien, sit amet adipiscing turpis gravida ac.</p>
    <span class="more">Read More</span>
  </div>
  <span class="btn all">Read All News</span>
  <div class="testimonial">
    <h2>TESTIMONIALS</h2>
    <blockquote>“ Sed accumsan sollicitudin sapien, sit amet adipiscing turpis gravida ac. In congue, neque ac lobortis volutpat, libero mauris varius mi, vitae suscipit ipsum ligula vitae risus. Duis aliquam nibh a dui iaculis viverra id a velit...”</blockquote>
    <div class="name">-Name Heading</div>
    <div class="co">Company Name</div>
    <span class="btn">Read More</span>
  </div>
</div>

<div class="section footer">
  <div class="f-brand">BRIGHT HARBOR VENTURE</div>
  <div class="f-legal">Copyright © 2016. Bright Harbor Venture Limited,<br>Registered in England and Wales.<br>Registeres number 10482915</div>
  <div class="f-social"><i></i><i></i><i></i><i></i><i></i></div>
  <div class="sitemap">
    <h5>Site Map</h5>
    <div class="links">
      <a>About You</a><a>News Alert</a>
      <a>About Us</a><a>Contact Us</a>
      <a>Our Values</a><span></span>
      <a>Testimonials</a><span></span>
    </div>
  </div>
  <div class="chat">
    <h5>Let's Chat</h5>
    <p>Let's chat, if you want a non committal conversation get in touch by email or telephone.</p>
    <div class="row"><svg width="13" height="13" viewBox="0 0 24 24"><path fill="#555" d="M6.6 10.8a15 15 0 0 0 6.6 6.6l2.2-2.2c.3-.3.7-.4 1-.2 1.1.4 2.3.6 3.6.6.6 0 1 .4 1 1V20c0 .6-.4 1-1 1A17 17 0 0 1 3 4c0-.6.4-1 1-1h3.5c.6 0 1 .4 1 1 0 1.3.2 2.5.6 3.6.1.3 0 .7-.2 1z"/></svg>+44 (0) 768 213 5597</div>
    <div class="row"><svg width="14" height="11" viewBox="0 0 26 20"><rect x="1" y="1" width="24" height="18" rx="2" fill="#555"/><path d="M2 3l11 8 11-8" stroke="#e4daeb" stroke-width="2" fill="none"/></svg>director@brightharborventure.com</div>
  </div>
</div>

</body>
</html>
```